Business Card Design for Property Development Company Director

I am looking for a professional and unforgettable business card design for our Director of our Property Development Company.
Please see attached .pptx file to find out what information to include. You don't have to follow the exact format shown in the file - I am interested to see your creative flair using the information provided.

```html
<!DOCTYPE html>
<html lang="en">
<head>
<meta charset="UTF-8">
<title>Halvern Property Group – Business Card</title>
<link href="https://fonts.googleapis.com/css2?family=Arimo:wght@400;700&display=swap" rel="stylesheet">
<style>
  :root {
    --bg: #1f2024;
    --card-grey: #6b6b6d;
    --card-white: #ffffff;
    --brand-blue: #0b55a5;
    --brand-grey: #5f5f61;
    --text-white: #ffffff;
  }
  * { box-sizing: border-box; margin: 0; padding: 0; }
  html, body {
    width: 1200px; height: 800px; overflow: hidden;
    background: var(--bg);
    font-family: "Arimo", Arial, sans-serif;
  }
  .canvas {
    width: 1200px; height: 800px;
    display: flex; flex-direction: column;
    align-items: center; justify-content: center; gap: 40px;
  }
  .card {
    width: 560px; height: 320px;
    position: relative; overflow: hidden;
  }

  /* Back side */
  .card-back {
    background: var(--card-grey);
    color: var(--text-white);
    display: flex; flex-direction: column;
    align-items: center; justify-content: center;
    text-align: center;
  }
  .tagline {
    font-weight: 700; font-size: 17px; line-height: 1.35;
    letter-spacing: 0.5px; text-transform: uppercase;
  }
  .back-brand {
    margin-top: 30px;
    display: flex; align-items: center; gap: 14px;
  }
  .brand-square {
    width: 34px; height: 34px; background: var(--text-white);
  }
  .back-brand .brand-name {
    font-weight: 700; font-size: 28px; line-height: 1.05;
    text-transform: uppercase; text-align: left;
  }
  .back-brand .brand-name small {
    display: block; font-size: 13px; letter-spacing: 4px;
  }
  .invite {
    margin-top: 36px; font-size: 11px; letter-spacing: 0.3px;
  }
  .invite strong { font-weight: 700; text-transform: uppercase; }

  /* Front side */
  .card-front {
    background: var(--card-white);
    display: flex; align-items: center;
    padding: 0 34px;
  }
  .details { flex: 1; }
  .front-brand {
    font-weight: 700; font-size: 34px; line-height: 1;
    color: var(--brand-grey); text-transform: uppercase;
  }
  .front-brand small {
    display: block; font-size: 12px; letter-spacing: 3.5px; margin-top: 3px;
  }
  .person { margin-top: 26px; }
  .person-name {
    font-weight: 700; font-size: 17px; color: var(--brand-grey);
    text-transform: uppercase;
  }
  .person-role { font-size: 14px; color: var(--brand-blue); margin-top: 2px; }
  .contact-list { list-style: none; margin-top: 12px; }
  .contact-list li {
    display: flex; align-items: center; gap: 8px;
    font-size: 12.5px; color: var(--brand-grey); line-height: 1.6;
  }
  .contact-list svg { width: 11px; height: 11px; fill: var(--brand-blue); }
  .licence { margin-top: 8px; font-size: 12px; color: var(--brand-blue); }

  .mark-area {
    width: 220px;
    display: flex; align-items: center; justify-content: center; gap: 12px;
  }
  .mark-square { width: 30px; height: 30px; background: var(--brand-blue); }
  .mark-name {
    font-weight: 700; font-size: 40px; color: var(--brand-grey);
    text-transform: uppercase;
  }
</style>
</head>
<body>
<main class="canvas">

  <section class="card card-back" aria-label="Card back">
    <p class="tagline">Property Development<br>&amp; Site Acquisition Specialists</p>
    <div class="back-brand">
      <span class="brand-square"></span>
      <p class="brand-name">Halvern<small>Property Group</small></p>
    </div>
    <p class="invite">Ask me about our <strong>Investment &amp; Partnership</strong> opportunities</p>
  </section>

  <section class="card card-front" aria-label="Card front">
    <div class="details">
      <p class="front-brand">Halvern<small>Property Group</small></p>
      <div class="person">
        <p class="person-name">Daniel Marsh</p>
        <p class="person-role">Director</p>
      </div>
      <ul class="contact-list">
        <li>
          <svg viewBox="0 0 12 12" aria-hidden="true"><path d="M2 1h2.5l1 3-1.5 1a7 7 0 0 0 3 3l1-1.5 3 1V10a1 1 0 0 1-1 1A9 9 0 0 1 1 2a1 1 0 0 1 1-1z"/></svg>
          0400 123 456
        </li>
        <li>
          <svg viewBox="0 0 12 12" aria-hidden="true"><path d="M1 2.5h10v7H1z M1 2.5l5 4 5-4" stroke="#fff" stroke-width="0.8"/></svg>
          daniel@halvern.com.au
        </li>
        <li>
          <svg viewBox="0 0 12 12" aria-hidden="true"><circle cx="6" cy="6" r="5"/><path d="M1 6h10M6 1v10" stroke="#fff" stroke-width="0.7"/></svg>
          www.halvern.com.au
        </li>
      </ul>
      <p class="licence">Real Estate Lic. 1234567 &amp; 1234568</p>
    </div>
    <div class="mark-area">
      <span class="mark-square"></span>
      <span class="mark-name">Halvern</span>
    </div>
  </section>

</main>
</body>
</html>
```